Business card design for my company.
I would like the card's background colour to be black. You can also see our web site to get an idea of our brand. https://www.tmwhomecrafting.com.au/
- Name
- Email

```html
<!DOCTYPE html>
<html lang="en">
<head>
<meta charset="utf-8">
<title>TMW Home Crafting — Business Card</title>
<link href="https://fonts.googleapis.com/css2?family=Montserrat:wght@400;500;700&display=swap" rel="stylesheet">
<style>
  :root {
    --bg: #b9b9b9;
    --card: #242424;
    --green: #1f9a45;
    --green-line: #1c6a35;
    --white: #f4f4f4;
    --muted: #d8d8d8;
  }
  * { margin: 0; padding: 0; box-sizing: border-box; }
  html, body {
    width: 1200px; height: 802px; overflow: hidden;
    background: linear-gradient(180deg, #d2d2d2, var(--bg));
    font-family: "Montserrat", Arial, sans-serif;
  }
  .stage {
    width: 1200px; height: 802px;
    display: flex; align-items: center; justify-content: center; gap: 40px;
  }
  .card {
    position: relative;
    width: 540px; height: 309px;
    background: var(--card);
    border-radius: 14px;
    overflow: hidden;
    box-shadow: 0 14px 30px rgba(0,0,0,.28);
  }
  .card--front::after {
    content: ""; position: absolute; left: 0; right: 0; bottom: 0;
    height: 7px; background: var(--green);
  }
  .wordmark {
    display: flex; align-items: center; gap: 8px;
    color: var(--white); font-weight: 700; text-transform: uppercase;
  }
  .wordmark__dot { background: var(--green); flex: none; }
  .card--front .wordmark {
    position: absolute; right: 30px; top: 34px;
    font-size: 15px; letter-spacing: 2px;
  }
  .card--front .wordmark__dot { width: 10px; height: 10px; }
  .person { position: absolute; left: 30px; top: 152px; }
  .person__name {
    color: var(--green); font-weight: 700; font-size: 16px;
    letter-spacing: .5px; text-transform: uppercase;
  }
  .person__role { color: var(--white); font-size: 11px; margin-top: 2px; }
  .divider {
    position: absolute; left: 30px; right: 30px; top: 196px;
    height: 1px; background: var(--green-line);
  }
  .contacts {
    position: absolute; left: 30px; top: 208px;
    list-style: none; display: grid; gap: 7px;
  }
  .contacts li {
    display: flex; align-items: center; gap: 8px;
    color: var(--muted); font-size: 11px;
  }
  .contacts svg { width: 11px; height: 11px; fill: var(--green); flex: none; }
  .card--back { display: flex; align-items: center; justify-content: center; }
  .card--back .wordmark { font-size: 26px; letter-spacing: 3px; gap: 12px; }
  .card--back .wordmark__dot { width: 16px; height: 16px; }
</style>
</head>
<body>
<main class="stage">
  <section class="card card--front" aria-label="Card front">
    <div class="wordmark"><span class="wordmark__dot"></span>TMW Home Crafting</div>
    <div class="person">
      <p class="person__name">Dorian Vale</p>
      <p class="person__role">CEO/Founder</p>
    </div>
    <div class="divider"></div>
    <ul class="contacts">
      <li>
        <svg viewBox="0 0 24 24" aria-hidden="true"><path d="M6.6 10.8a15.1 15.1 0 0 0 6.6 6.6l2.2-2.2a1 1 0 0 1 1-.25 11.4 11.4 0 0 0 3.6.57 1 1 0 0 1 1 1V20a1 1 0 0 1-1 1A17 17 0 0 1 3 4a1 1 0 0 1 1-1h3.5a1 1 0 0 1 1 1c0 1.25.2 2.45.57 3.57a1 1 0 0 1-.25 1z"/></svg>
        555-214-7390
      </li>
      <li>
        <svg viewBox="0 0 24 24" aria-hidden="true"><path d="M2 5h20v14H2zm2 2v.5l8 5 8-5V7l-8 5z"/></svg>
        info@tmwhomecrafting.com.au
      </li>
      <li>
        <svg viewBox="0 0 24 24" aria-hidden="true"><circle cx="12" cy="12" r="10"/></svg>
        www.tmwhomecrafting.com.au
      </li>
    </ul>
  </section>

  <section class="card card--back" aria-label="Card back">
    <div class="wordmark"><span class="wordmark__dot"></span>TMW Home Crafting</div>
  </section>
</main>
</body>
</html>
```